I would like a business card to match my truck wrap and logo. I would like the font to match my existing business card please.

Industry/Entity Type

Painter

Contact Information for Business Card

Rodrigo Fenwar 801-437-2190 Fenwarcoatings.utah@brelmox.com
SERVICES - Custom Paint & Stain, Interior & Exterior, Epoxy Coatings / Garage Floors, Cabinet Refinishing, Log Staining and Refinishing.

Requirements
Nice to have
• I would like to have the white and grey line like the bottom of my vehicle wrap, Light Grey to match my truck also.

```html
<!DOCTYPE html>
<html lang="en">
<head>
<meta charset="utf-8">
<title>Fenwar Painting — Business Card</title>
<link rel="stylesheet" href="https://fonts.googleapis.com/css2?family=Arimo:wght@400;700&family=Oswald:wght@500&display=swap">
<style>
  :root {
    --backdrop: #0b0b0b;
    --card: #171717;
    --accent: #16a6ec;
    --accent-deep: #0d7fc4;
    --text-grey: #b9b9b9;
    --rule-grey: #8a8a8a;
  }
  * { margin: 0; padding: 0; box-sizing: border-box; }
  html, body {
    width: 1200px; height: 900px; overflow: hidden;
    background: var(--backdrop);
  }
  .canvas {
    width: 1200px; height: 900px;
    display: flex; flex-direction: column; align-items: center; justify-content: center;
    gap: 44px;
  }
  .card {
    position: relative;
    width: 640px; height: 366px;
    background: var(--card);
    box-shadow: 0 10px 30px rgba(0,0,0,.7);
    overflow: hidden;
  }
  .card__band {
    position: absolute; left: 0; right: 0; bottom: 0;
    height: 10px;
    background: linear-gradient(var(--accent), var(--accent-deep));
  }

  /* Front */
  .front__brand {
    position: absolute; top: 92px; left: 0; right: 0;
    display: flex; align-items: center; justify-content: center; gap: 16px;
  }
  .brand__mark {
    flex: none;
    width: 34px; height: 34px;
    background: var(--accent);
  }
  .brand__name {
    font-family: "Arimo", Arial, sans-serif;
    font-weight: 700;
    font-size: 40px;
    letter-spacing: 2px;
    text-transform: uppercase;
    color: var(--accent);
  }
  .front__services {
    position: absolute; top: 192px; left: 0; right: 0;
    text-align: center;
    font-family: "Arimo", Arial, sans-serif;
    font-size: 17px;
    line-height: 1.45;
    color: var(--text-grey);
  }
  .dot {
    display: inline-block;
    width: 8px; height: 8px; border-radius: 50%;
    background: var(--accent);
    margin: 0 6px; vertical-align: 2px;
  }

  /* Back */
  .back__body {
    position: absolute; top: 130px; left: 36px; right: 36px;
    display: flex; align-items: center; gap: 22px;
  }
  .back__name {
    flex: none;
    font-family: "Oswald", "Arial Narrow", sans-serif;
    font-weight: 500;
    font-size: 34px;
    text-transform: uppercase;
    letter-spacing: -0.5px;
    color: var(--accent);
    white-space: nowrap;
  }
  .back__divider {
    flex: none;
    width: 1px; height: 62px;
    background: var(--rule-grey);
  }
  .back__contacts {
    flex: none;
    list-style: none;
    font-family: "Arimo", Arial, sans-serif;
    font-size: 15px;
    color: var(--text-grey);
    line-height: 1.75;
    white-space: nowrap;
  }
  .contact { display: flex; align-items: center; gap: 8px; }
  .contact svg { width: 15px; height: 15px; fill: var(--accent); flex: none; }
</style>
</head>
<body>
<main class="canvas">
  <section class="card card--front">
    <div class="front__brand">
      <span class="brand__mark"></span>
      <span class="brand__name">Fenwar Painting</span>
    </div>
    <p class="front__services">
      Custom Paint &amp; Stain<span class="dot"></span>Interior &amp; Exterior<br>
      Epoxy Coatings / Garage Floors<span class="dot"></span>Cabinet Refinishing<br>
      Log Staining and Refinishing.
    </p>
    <div class="card__band"></div>
  </section>

  <section class="card card--back">
    <div class="back__body">
      <h1 class="back__name">Rodrigo Fenwar</h1>
      <span class="back__divider"></span>
      <ul class="back__contacts">
        <li class="contact">
          <svg viewBox="0 0 24 24" aria-hidden="true"><path d="M6.6 10.8a15.1 15.1 0 0 0 6.6 6.6l2.2-2.2c.3-.3.7-.4 1-.2 1.1.4 2.3.6 3.6.6.6 0 1 .4 1 1V20c0 .6-.4 1-1 1A17 17 0 0 1 3 4c0-.6.4-1 1-1h3.5c.6 0 1 .4 1 1 0 1.3.2 2.5.6 3.6.1.3 0 .7-.2 1z"/></svg>
          <span>801-437-2190</span>
        </li>
        <li class="contact">
          <svg viewBox="0 0 24 24" aria-hidden="true"><path d="M2 5h20v14H2zM3.5 6.5 12 13l8.5-6.5z" fill-rule="evenodd"/></svg>
          <span>Fenwarcoatings.utah@brelmox.com</span>
        </li>
      </ul>
    </div>
    <div class="card__band"></div>
  </section>
</main>
</body>
</html>
```